Quorva - corporate Business Card

We need a good look and innovative business card for a new start up company based in Los Angeles called "Quorva". We are in a payment business, including payment card, app, and ewallet. We are expert in online payment and Card not present (CNP) transaction.
We need an innovative, modern business card.

Our logo font is Aero Matics

Target Market(s)

Startup - Bank - Online Payment - Card Manufacturing

Industry/Entity Type

Startup

Contact Information for Business Card

phone: 555 014 7396 - Address: 4172 Marlowe blvd, Halvern City, OR 97299

Requirements
Must have
• Message: innovative, professional, expert, high tech, trust, online payment expert, security
Nice to have
• no comment
Should not have
• no Comment

```html
<!DOCTYPE html>
<html lang="en">
<head>
<meta charset="utf-8">
<title>Quorva – Business Card</title>
<link rel="stylesheet" href="https://fonts.googleapis.com/css2?family=Open+Sans:wght@400;600;700&display=swap">
<style>
  :root {
    --backdrop: #222222;
    --brand-red: #b8202e;
    --paper: #ffffff;
    --text-grey: #7b7b7b;
  }
  * { margin: 0; padding: 0; box-sizing: border-box; }
  html, body {
    width: 1189px;
    height: 1200px;
    overflow: hidden;
    background: var(--backdrop);
    font-family: "Open Sans", Arial, sans-serif;
  }
  .card {
    position: absolute;
    left: 171px;
    width: 855px;
    height: 487px;
    box-shadow: 2px 3px 6px rgba(0,0,0,0.55);
  }
  .card--front { top: 68px; background: var(--brand-red); color: var(--paper); }
  .card--back { top: 625px; background: var(--paper); color: var(--brand-red); }
  .card__frame {
    position: absolute;
    inset: 0;
    width: 100%;
    height: 100%;
  }
  .card__frame path { fill: none; stroke-width: 2; }
  .card--front .card__frame path { stroke: var(--paper); }
  .card--back .card__frame path { stroke: var(--brand-red); }

  .brand {
    position: absolute;
    left: 216px;
    display: flex;
    align-items: center;
    gap: 14px;
  }
  .card--front .brand { top: 180px; }
  .card--back .brand { top: 62px; }
  .brand__dot {
    width: 128px;
    height: 128px;
    border-radius: 50%;
    flex: none;
  }
  .card--front .brand__dot { background: var(--paper); }
  .card--back .brand__dot { background: var(--brand-red); }
  .brand__name {
    font-weight: 600;
    font-size: 84px;
    line-height: 1;
    letter-spacing: 0.5px;
  }

  .person {
    position: absolute;
    top: 230px;
    left: 0;
    width: 100%;
    text-align: center;
  }
  .person__name {
    font-weight: 700;
    font-size: 29px;
    line-height: 34px;
    color: var(--brand-red);
  }
  .person__role {
    font-weight: 400;
    font-size: 23px;
    line-height: 24px;
    color: var(--text-grey);
    letter-spacing: 0.3px;
  }
  .contact {
    position: absolute;
    top: 356px;
    left: 0;
    width: 100%;
    text-align: center;
    color: var(--text-grey);
    font-size: 23px;
  }
  .contact__address { line-height: 32px; }
  .contact__phone {
    margin-top: 9px;
    display: inline-flex;
    align-items: center;
    gap: 6px;
    line-height: 32px;
  }
  .contact__icon { width: 27px; height: 27px; }
</style>
</head>
<body>

<section class="card card--front" aria-label="Card front">
  <svg class="card__frame" viewBox="0 0 855 487" aria-hidden="true">
    <path d="M52,14 H803 A38 38 0 0 0 841,52 V435 A38 38 0 0 0 803,473 H52 A38 38 0 0 0 14,435 V52 A38 38 0 0 0 52,14 Z"/>
    <path d="M54,24 H801 A30 30 0 0 0 831,54 V433 A30 30 0 0 0 801,463 H54 A30 30 0 0 0 24,433 V54 A30 30 0 0 0 54,24 Z"/>
  </svg>
  <div class="brand">
    <span class="brand__dot"></span>
    <span class="brand__name">Quorva</span>
  </div>
</section>

<section class="card card--back" aria-label="Card back">
  <svg class="card__frame" viewBox="0 0 855 487" aria-hidden="true">
    <path d="M52,14 H803 A38 38 0 0 0 841,52 V435 A38 38 0 0 0 803,473 H52 A38 38 0 0 0 14,435 V52 A38 38 0 0 0 52,14 Z"/>
    <path d="M54,24 H801 A30 30 0 0 0 831,54 V433 A30 30 0 0 0 801,463 H54 A30 30 0 0 0 24,433 V54 A30 30 0 0 0 54,24 Z"/>
  </svg>
  <div class="brand">
    <span class="brand__dot"></span>
    <span class="brand__name">Quorva</span>
  </div>
  <div class="person">
    <p class="person__name">Marcus Hale</p>
    <p class="person__role">Managing Director</p>
  </div>
  <div class="contact">
    <p class="contact__address">4172 Marlowe blvd, Halvern City, OR 97299</p>
    <p class="contact__phone">
      <svg class="contact__icon" viewBox="0 0 28 28" aria-hidden="true">
        <circle cx="14" cy="14" r="14" fill="#b8202e"/>
        <path d="M6 12 Q14 6 22 12 L20.5 14 L17.5 13 L17 11 Q14 10 11 11 L10.5 13 L7.5 14 Z" fill="#fff"/>
        <rect x="9" y="15" width="10" height="6" rx="1.5" fill="#fff"/>
      </svg>
      <span>555 014 7396</span>
    </p>
  </div>
</section>

</body>
</html>
```